Flyer-Design für trommel-welt
Zielgruppe
Website und Onlineshop rund um die irische Rahmentrommel 'bodhrán'. Wir bieten Informationen, Kaufberatung und einen Onlineshop. Wir sind auf Qualitätsinstrumente spezialisiert und verkaufen keine billigen Instrumente aus Fernost.
Aufgabenstellung
Wir haben die Website komplett neu gestaltet und brauchen nun einen neuen Flyer im Stil der Website. Die Adresse ist www.trommel-welt.de Es müsste also auf den Bildern und ungefähr dem Design der Website beruhen. Die Bilder kann ich dann natürlich zur Verfügung stellen. Beim Format würde ich gerne etwas kleineres längliches nehmen und auf 300er Recycling Papier drucken. Hatte vorher DIN lang, aber ich habe hier Flyer in 14*6,5 cm gesehen, die fand ich auch schön.
Die Seite ist deutsch und englisch, daher sollte der Flyer eine Seite deutsch, eine Seite englisch haben.

```html
<!DOCTYPE html>
<html lang="de">
<head>
<meta charset="utf-8">
<title>trommel-welt Flyer</title>
<link rel="stylesheet" href="https://fonts.googleapis.com/css2?family=Roboto:wght@300;500;700&display=swap">
<style>
  :root {
    --brand-red: #9e2a14;
    --brand-red-deep: #8a2210;
    --ink: #111111;
    --muted: #555555;
    --paper: #ffffff;
    --footer: #000000;
  }
  * { margin: 0; padding: 0; box-sizing: border-box; }
  html, body { width: 1200px; height: 2584px; overflow: hidden; background: var(--paper); }
  .flyer { position: relative; width: 1200px; height: 2584px; font-family: "Roboto", Arial, sans-serif; color: var(--ink); overflow: hidden; }

  .hero { position: absolute; left: 0; top: 0; width: 1200px; height: 900px; }

  .brand-name { position: absolute; left: 130px; top: 790px; font-weight: 700; font-size: 112px; line-height: 130px; color: var(--brand-red); letter-spacing: -1px; white-space: nowrap; }

  .intro { position: absolute; left: 130px; top: 1010px; width: 850px; font-weight: 500; font-size: 47px; line-height: 62.5px; }

  .section-head { position: absolute; left: 125px; display: flex; align-items: center; gap: 36px; }
  .section-head svg { flex: none; }
  .section-title { font-weight: 500; font-size: 59px; color: var(--ink); }

  .checklist { position: absolute; left: 126px; list-style: none; font-weight: 300; font-size: 49px; line-height: 62.5px; color: var(--muted); }
  .checklist li { position: relative; padding-left: 82px; }
  .checklist li svg { position: absolute; left: 0; top: 18px; }

  .web { position: absolute; right: 130px; top: 2260px; font-weight: 500; font-size: 49px; color: var(--ink); }

  .footer { position: absolute; left: 0; top: 2380px; width: 1200px; height: 204px; background: var(--footer); color: var(--paper); }
  .partner { position: absolute; left: 126px; top: 60px; text-align: center; font-weight: 700; color: var(--paper); }
  .partner-name { font-size: 44px; letter-spacing: 1px; line-height: 48px; }
  .partner-level { font-size: 30px; letter-spacing: 1px; line-height: 36px; }
  .ally { position: absolute; right: 130px; top: 54px; font-weight: 700; font-size: 82px; line-height: 100px; color: var(--paper); }
</style>
</head>
<body>
<div class="flyer">

  <svg class="hero" viewBox="0 0 1200 900">
    <defs>
      <linearGradient id="drumTones" x1="0" y1="0" x2="1" y2="0">
        <stop offset="0" stop-color="#c9b9a4"/>
        <stop offset="0.18" stop-color="#b8441f"/>
        <stop offset="0.4" stop-color="#c0502a"/>
        <stop offset="0.55" stop-color="#2d3440"/>
        <stop offset="0.72" stop-color="#8e7460"/>
        <stop offset="0.88" stop-color="#b96a35"/>
        <stop offset="1" stop-color="#d9b98a"/>
      </linearGradient>
    </defs>
    <path role="img" aria-label="Foto: Reihe handgefertigter Bodhráns mit Holzrahmen" d="M0,0 H1200 V465 Q600,790 0,422 Z" fill="url(#drumTones)"/>
    <path class="swoosh" d="M0,422 Q600,790 1200,465 L1200,472 Q600,864 0,555 Z" fill="var(--brand-red-deep)"/>
  </svg>

  <div class="brand-name">trommel-welt</div>

  <p class="intro">Wir bieten individuelle Beratung, die auf einer 30-jährigen Erfahrung im professionellem Bodhránspiel und Unterricht aufbaut.</p>

  <div class="section-head" style="top:1322px;">
    <svg width="94" height="92" viewBox="0 0 94 92" fill="none" stroke="var(--brand-red)" stroke-width="4">
      <path d="M6,24 L47,4 L88,24 Z"/>
      <rect x="6" y="26" width="82" height="8"/>
      <path d="M16,38 V76 M30,38 V76 M44,38 V76 M58,38 V76 M72,38 V76 M80,38 V76"/>
      <rect x="6" y="78" width="82" height="10"/>
    </svg>
    <span class="section-title">Die irische Rahmentrommel</span>
  </div>
  <ul class="checklist" style="top:1473px;">
    <li><svg width="44" height="32" viewBox="0 0 44 32"><path d="M3,16 L16,28 L41,3" fill="none" stroke="var(--brand-red)" stroke-width="5"/></svg>Alles über die Bodhrán</li>
    <li><svg width="44" height="32" viewBox="0 0 44 32"><path d="M3,16 L16,28 L41,3" fill="none" stroke="var(--brand-red)" stroke-width="5"/></svg>Ratgeber zum Bodhránkauf</li>
    <li><svg width="44" height="32" viewBox="0 0 44 32"><path d="M3,16 L16,28 L41,3" fill="none" stroke="var(--brand-red)" stroke-width="5"/></svg>Infos über Tipper, Geschichte<br>und Konstruktion</li>
  </ul>

  <div class="section-head" style="top:1786px;">
    <svg width="86" height="82" viewBox="0 0 86 82" fill="none" stroke="var(--brand-red)" stroke-width="4">
      <rect x="3" y="3" width="80" height="8"/>
      <path d="M3,11 V28 Q13,34 23,28 Q33,34 43,28 Q53,34 63,28 Q73,34 83,28 V11"/>
      <path d="M23,11 V28 M43,11 V28 M63,11 V28"/>
      <path d="M6,32 V79 H80 V32"/>
      <rect x="14" y="44" width="30" height="22"/>
      <path d="M54,79 V44 H72 V79"/>
    </svg>
    <span class="section-title">Online Shop</span>
  </div>
  <ul class="checklist" style="top:1930px;">
    <li><svg width="44" height="32" viewBox="0 0 44 32"><path d="M3,16 L16,28 L41,3" fill="none" stroke="var(--brand-red)" stroke-width="5"/></svg>Handgefertigte Bodhráns und Tipper</li>
    <li><svg width="44" height="32" viewBox="0 0 44 32"><path d="M3,16 L16,28 L41,3" fill="none" stroke="var(--brand-red)" stroke-width="5"/></svg>ExpressKonfigurator zum<br>Konfigurieren individueller Bodhráns</li>
    <li><svg width="44" height="32" viewBox="0 0 44 32"><path d="M3,16 L16,28 L41,3" fill="none" stroke="var(--brand-red)" stroke-width="5"/></svg>Taschen, Zubehör, Lernmaterial<br>und CDs</li>
  </ul>

  <div class="web">www.trommel-welt.de</div>

  <footer class="footer">
    <div class="partner">
      <div class="partner-name">KELLMANN DRUMS</div>
      <div class="partner-level">PREMIUM PARTNER</div>
    </div>
    <div class="ally">tarvo</div>
  </footer>

</div>
</body>
</html>
```